Need a Wordpress website for my HVAC company

I need a Wordpress website created for an HVAC company in a competitive market.
Following are some websites I like:
My current website is www.borvicoheating.com - we also have a facebook page with some pictures

We are an airconditioning and heating company that does both residential and commmercial work.
We need the following info on our website:
-mobile friendly
-Schedule an appt -repair/maintnenace/installation (i would like this option to always be on the page even if they scroll down.)
-24 hour service
-coupons /promotions
-financing
-reviews/testimonials
-about
-blog
-Our service area
The following are services we provide:
-Air conditioning - Installation/Service/Maintenance/new construction
-Heating - Installation/Service/Maintenance/new construction ( gas furnace, 2 stage furnace, electric heat)
-Duct - Repair/Replacement/Istallation - (zone systems)
-thermostats (wifi)
-Heat pump
-Air handler
-self communicating systems
-carbon monoxide testing
-hail damage
-duct sealing
-insulation
-Air cleaners - UV Air purifiers
-humidifiers

I would also like Quilbo SEO add on

Target Market(s)

Anyone who needs our services HVAC contractor

Industry/Entity Type

Hvac

Contact Information for Business Card

Phone:480-555-2046
website:www.borvicoheating.com
email pmarsh@borvicoheating.com

Coding

Coded - Design and coding required

Number of Pages Required

5+ page

Font styles to use
Serif
Sans Serif

Requirements
Must have
• I wrote in brief. I already have Webly Nest. Long story I paid for 3 years already. I need someone to put website there. Ive never used Wordpress but would like a template page so I can easily add services.
Nice to have
• Clean, bright, original

```html
<!DOCTYPE html>
<html lang="en">
<head>
<meta charset="utf-8">
<title>Borvico Heating – HVAC Services</title>
<link href="https://fonts.googleapis.com/css2?family=Roboto:ital,wght@0,400;0,500;0,700;1,400&family=Roboto+Condensed:wght@400;700&family=Nothing+You+Could+Do&display=swap" rel="stylesheet">
<style>
:root{
  --blue:#1b6fbd;
  --blue-light:#2398e2;
  --blue-dark:#14589c;
  --navy:#1a4f8b;
  --red:#d32027;
  --green:#35a23a;
  --slate:#414850;
  --grey-hero:#cfcdc9;
  --grey-hero-light:#dedcd8;
  --ink:#222;
  --muted:#555;
  --white:#fff;
  --dot:#3a7cc4;
}
*{box-sizing:border-box;margin:0;padding:0}
html,body{width:1200px;height:2190px;overflow:hidden}
body{font-family:"Roboto",Arial,sans-serif;color:var(--ink);background:var(--white);position:relative}
.abs{position:absolute}

/* header */
.utility{position:absolute;top:0;left:0;width:1200px;height:35px}
.utility .phone{position:absolute;left:555px;top:8px;font-size:14px;color:#777;display:flex;align-items:center;gap:5px}
.pill{position:absolute;top:5px;height:22px;border-radius:6px;color:#fff;font:700 14px "Roboto Condensed",sans-serif;line-height:22px;padding:0 8px}
.pill.repair{left:706px;background:var(--red)}
.pill.maint{left:790px;background:var(--green)}
.pill.install{left:925px;background:var(--navy)}
.utility .social{position:absolute;top:10px;width:13px;height:13px;border-radius:50%;background:#9a9a9a}
.navbar{position:absolute;top:35px;left:0;width:1200px;height:69px;background:linear-gradient(90deg,var(--blue),var(--blue-light))}
.navbar ul{list-style:none;position:absolute;right:16px;top:0;height:69px;display:flex;align-items:center;gap:37px}
.navbar li{color:#fff;font:700 16px "Roboto Condensed",sans-serif;text-transform:uppercase}
.logo-box{position:absolute;left:54px;top:0;width:283px;height:134px;background:#fff;border-radius:0 0 8px 8px;display:flex;align-items:center;justify-content:center;gap:10px;box-shadow:0 2px 6px rgba(0,0,0,.12)}
.logo-box .mark{width:22px;height:22px;border-radius:50%;background:var(--red)}
.logo-box .name{font:700 34px "Roboto Condensed",sans-serif;color:var(--navy);letter-spacing:1px}

/* hero */
.hero{position:absolute;top:104px;left:0;width:1200px;height:492px;background:linear-gradient(115deg,var(--grey-hero) 0%,var(--grey-hero) 55%,var(--grey-hero-light) 55%,var(--grey-hero-light) 100%)}
.hero h1{position:absolute;left:63px;top:96px;font:400 60px/62px "Nothing You Could Do",cursive;color:#fff}
.hero p{position:absolute;left:63px;top:216px;width:450px;font:400 21px/28px "Roboto Condensed",sans-serif;color:#fff}
.hero .call{position:absolute;left:63px;top:311px;height:34px;padding:0 15px;background:#fff;border-radius:3px;color:var(--blue);font:700 11px/34px "Roboto",sans-serif}
.mascot{position:absolute;left:745px;top:6px;width:250px;height:380px;border-radius:60px 60px 20px 20px;background:linear-gradient(180deg,#5b8cc2,#2c4f86)}

/* service cards */
.card{position:absolute;top:525px;width:349px;height:135px;background:linear-gradient(180deg,#9fb8cf,#7a8a6f)}
.card.c1{left:51px}.card.c2{left:426px;background:linear-gradient(180deg,#9cc4e8,#b7b3a8)}.card.c3{left:801px;background:linear-gradient(180deg,#7da6cf,#5d4b3c)}
.card-label{position:absolute;top:636px;width:319px;height:46px;border-radius:3px;background:linear-gradient(90deg,var(--blue),var(--blue-light));color:#fff;font:500 17px/46px "Roboto",sans-serif;text-align:center;text-transform:uppercase;box-shadow:0 3px 6px rgba(0,0,0,.2)}
.card-icon{position:absolute;top:502px;width:46px;height:46px;border-radius:50%;background:var(--blue);border:3px solid #fff;display:flex;align-items:center;justify-content:center}

/* about + mail */
.about{position:absolute;top:714px;left:0;width:600px;height:304px;background:linear-gradient(135deg,var(--blue-dark),var(--blue-light));color:#fff;text-align:center}
.about h2,.mail h2{font:500 27px "Roboto",sans-serif;margin-top:35px}
.about p{width:510px;margin:22px auto 0;font-size:14px;line-height:22px}
.btn-outline{display:inline-block;margin-top:22px;border:1px solid #fff;border-radius:3px;padding:0 17px;height:34px;line-height:34px;font:700 12px "Roboto",sans-serif}
.mail{position:absolute;top:714px;left:600px;width:600px;height:304px;background:var(--slate);color:#fff;text-align:center}
.field{position:absolute;background:#fff;border-radius:2px;color:#999;font-size:12px;text-align:left;padding:9px 14px}
.send{position:absolute;left:233px;top:257px;width:135px;height:34px;background:#fff;border-radius:3px;color:var(--ink);font:500 13px/34px "Roboto",sans-serif}

/* section titles */
.section-title{position:absolute;left:0;width:1200px;text-align:center;font:700 21px "Roboto",sans-serif;color:var(--ink)}
.section-title span{color:var(--blue)}
.dotted{position:absolute;left:54px;width:1095px;border-top:2px dotted var(--dot)}

/* projects */
.project{position:absolute;top:1104px;width:240px;height:179px}

/* testimonials */
.quote{position:absolute;width:410px;font:italic 400 13px/20px "Roboto",sans-serif;color:var(--muted)}
.quote.left{text-align:right}
.who{position:absolute;font:500 13px "Roboto",sans-serif;color:var(--ink)}
.avatar{position:absolute;width:78px;height:78px;border-radius:50%}
.vline{position:absolute;left:599px;top:1417px;height:218px;border-left:2px dotted var(--dot)}

/* like strip */
.like-strip{position:absolute;top:1701px;left:0;width:1200px;height:76px;background:#f4f4f4}
.like-strip .rule{position:absolute;left:63px;width:1074px;top:38px;border-top:1px solid #ddd}
.like-pill{position:absolute;left:377px;top:15px;width:448px;height:46px;border:1px solid #ddd;border-radius:23px;background:#fff;display:flex;align-items:center}
.like-pill .thumb{width:58px;height:100%;border-right:1px solid #ddd;display:flex;align-items:center;justify-content:center}
.like-pill .btn{margin-left:12px;width:44px;height:16px;background:#5b7fc7;border-radius:2px}
.like-pill .txt{margin-left:8px;font-size:11px;color:#333}

/* footer */
.footer{position:absolute;top:1777px;left:0;width:1200px;height:413px;background:linear-gradient(135deg,var(--blue-dark),var(--blue-light));color:#fff}
.footer h3{position:absolute;top:44px;font:700 18px "Roboto",sans-serif}
.footer .contact{position:absolute;left:52px;top:84px;width:265px;font-size:13px;line-height:19px}
.footer .contact p{margin-bottom:14px}
.footer .social-row{position:absolute;left:52px;top:265px;display:flex;gap:14px}
.footer .social-row i{width:14px;height:14px;border-radius:50%;background:#fff;display:block}
.map{position:absolute;left:333px;top:84px;width:534px;height:206px;background:linear-gradient(135deg,#f2e6c9,#cfe0f0 60%,#e9e4d8)}
.post{position:absolute;left:896px;display:flex;gap:15px}
.post .thumb{width:46px;height:46px;border-radius:50%;background:linear-gradient(135deg,#8a6a52,#d8cfc4);flex:none}
.post .t{font-size:13px;margin-top:2px}
.post .d{font-size:11px;margin-top:7px;opacity:.9}
.footer .divider{position:absolute;left:52px;width:1097px;top:343px;border-top:1px solid rgba(255,255,255,.45)}
.footer .copy{position:absolute;top:371px;width:1200px;text-align:center;font:500 12px "Roboto",sans-serif}
</style>
</head>
<body>

<header>
  <div class="utility">
    <div class="phone">
      <svg width="13" height="13" viewBox="0 0 24 24"><path fill="#888" d="M6.6 10.8a15 15 0 0 0 6.6 6.6l2.2-2.2c.3-.3.7-.4 1-.2 1.1.4 2.3.6 3.6.6.6 0 1 .4 1 1V20c0 .6-.4 1-1 1A17 17 0 0 1 3 4c0-.6.4-1 1-1h3.5c.6 0 1 .4 1 1 0 1.3.2 2.5.6 3.6.1.3 0 .7-.2 1z"/></svg>
      +1 800 555 01 47
    </div>
    <span class="pill repair">REPAIR</span>
    <span class="pill maint">MAINTNENACE</span>
    <span class="pill install">INSTALLATION</span>
    <span class="social" style="left:1056px"></span>
    <span class="social" style="left:1092px"></span>
    <svg class="abs" style="left:1130px;top:9px" width="15" height="15" viewBox="0 0 24 24"><circle cx="10" cy="10" r="6.5" fill="none" stroke="#888" stroke-width="2.6"/><line x1="15" y1="15" x2="21" y2="21" stroke="#888" stroke-width="3"/></svg>
  </div>
  <nav class="navbar">
    <ul>
      <li>Home</li><li>About Us</li><li>Our Services</li><li>Blog</li><li>Testimonials</li><li>Contact Us</li>
    </ul>
  </nav>
  <div class="logo-box"><span class="mark"></span><span class="name">BORVICO</span></div>
</header>

<section class="hero">
  <h1>High<br>Standards</h1>
  <p>Our Success is not Only Due to the Quality of Our Work. It's Down to Attitude, Our Approach and the Way We Treat Our Clients</p>
  <div class="call">CALL (480) 555-2046</div>
  <div class="mascot" role="img" aria-label="Cartoon technician in blue uniform holding a thermometer and giving a thumbs up"></div>
</section>

<section class="services">
  <div class="card c1" role="img" aria-label="Residential air conditioning unit beside a house"></div>
  <div class="card c2" role="img" aria-label="Commercial rooftop HVAC units"></div>
  <div class="card c3" role="img" aria-label="House roof with solar panels"></div>
  <div class="card-icon" style="left:202px">
    <svg width="22" height="22" viewBox="0 0 24 24"><path d="M3 12 12 4l9 8M6 10v10h12V10" fill="none" stroke="#fff" stroke-width="2"/><rect x="10" y="14" width="4" height="6" fill="#fff"/></svg>
  </div>
  <div class="card-icon" style="left:577px">
    <svg width="22" height="22" viewBox="0 0 24 24"><rect x="5" y="4" width="14" height="17" fill="none" stroke="#fff" stroke-width="2"/><path d="M8 8h2M14 8h2M8 12h2M14 12h2M8 16h2M14 16h2" stroke="#fff" stroke-width="2"/></svg>
  </div>
  <div class="card-icon" style="left:952px">
    <svg width="22" height="22" viewBox="0 0 24 24"><circle cx="12" cy="10" r="6" fill="none" stroke="#fff" stroke-width="2"/><path d="M9 18h6M10 21h4" stroke="#fff" stroke-width="2"/></svg>
  </div>
  <div class="card-label" style="left:66px">Residential</div>
  <div class="card-label" style="left:441px">Commercial</div>
  <div class="card-label" style="left:816px">Energy</div>
</section>

<section class="about">
  <h2>About Us</h2>
  <p>Borvico Heating is an Air Conditioning company located in Queen Creek, AZ. Borvico Heating provides air conditioning repair, service, maintenance and installation to both residential and commercial customers. We provide air conditioning repair, maintenance and installation in Queen Creek, Mesa, Chandler, Apache Junction, Gilbert, Tempe, Phoenix, Scottsdale and in the West Valley.</p>
  <span class="btn-outline">LEARN MORE</span>
</section>

<section class="mail">
  <h2>Feel Free to Mail</h2>
  <div class="field" style="left:49px;top:90px;width:154px;height:32px">Name *</div>
  <div class="field" style="left:223px;top:90px;width:154px;height:32px">Email *</div>
  <div class="field" style="left:397px;top:90px;width:154px;height:32px">Subject</div>
  <div class="field" style="left:49px;top:141px;width:502px;height:96px">Write Your Message Here...</div>
  <div class="send">SEND MESSAGE</div>
</section>

<h2 class="section-title" style="top:1036px">Latest <span>Projects</span></h2>
<div class="dotted" style="top:1074px"></div>
<div class="project" style="left:0;background:linear-gradient(180deg,#6d5d4a,#3a3026)" role="img" aria-label="HVAC equipment outside a retail store"></div>
<div class="project" style="left:240px;background:linear-gradient(180deg,#2f6fb8,#c9b8a0)" role="img" aria-label="Rooftop units under a blue sky"></div>
<div class="project" style="left:480px;background:linear-gradient(180deg,#a69e90,#5a5650)" role="img" aria-label="Condenser unit beside a house wall"></div>
<div class="project" style="left:720px;background:linear-gradient(180deg,#7b8f9c,#8c6d58)" role="img" aria-label="Packaged unit on a tiled roof"></div>
<div class="project" style="left:960px;background:linear-gradient(180deg,#5f7ea0,#c8ced6)" role="img" aria-label="Metal ductwork installation in a ceiling"></div>

<h2 class="section-title" style="top:1319px">What <span>People Say</span></h2>
<div class="dotted" style="top:1357px"></div>

<section class="testimonials">
  <p class="quote left" style="left:52px;top:1412px">At vero eos et accusamus et iusto odio dignissimos ducimus qui blanditiis praesentium voluptatum deleniti atque corrupti quos dolores et quas molestias excepturi sint occaecati.</p>
  <div class="who" style="left:332px;top:1485px">Owen Pratt , Developer</div>
  <div class="avatar" style="left:490px;top:1413px;background:linear-gradient(135deg,#c9a58a,#6b5444)" role="img" aria-label="Portrait of Owen Pratt"></div>

  <div class="avatar" style="left:632px;top:1413px;background:linear-gradient(135deg,#b98a62,#4e3626)" role="img" aria-label="Portrait of Nora Hale"></div>
  <p class="quote" style="left:739px;top:1412px">Luis aute irure dolor in reprehenderit in piluptate velit esse cillum dolore eu fugiat nulla pariatur. Excepteur sint occaecat cupidatat non proident, sunt in culpa qui officia deserunt mollit.</p>
  <div class="who" style="left:739px;top:1485px">Nora Hale , Manager</div>

  <div class="dotted" style="top:1524px"></div>
  <div class="vline"></div>

  <p class="quote left" style="left:52px;top:1550px">Provident, similique sunt in culpa qui officia deserunt mollitia animi, id est laborum et dolorum fuga. Et harum quidem rerum facilis est et expedita distinctio. Nam libero tempore, cum soluta nobis.</p>
  <div class="who" style="left:287px;top:1623px">Iris Vane , Creative Designer</div>
  <div class="avatar" style="left:490px;top:1551px;background:linear-gradient(135deg,#a87a5c,#3a2a20)" role="img" aria-label="Portrait of Iris Vane"></div>

  <div class="avatar" style="left:632px;top:1551px;background:linear-gradient(135deg,#c0a28c,#3d3029)" role="img" aria-label="Portrait of Reid Callum"></div>
  <p class="quote" style="left:739px;top:1550px">Duis aute irure dolor in reprehenderit in voluptate velit esse cillum dolore eu fugiat nulla pariatur. Excepteur sint occaecat cupidatat non proident, sunt in culpa qui officia deserunt mollit.</p>
  <div class="who" style="left:739px;top:1623px">Reid Callum , Operations Manager</div>
</section>

<section class="like-strip">
  <div class="rule"></div>
  <div class="like-pill">
    <div class="thumb">
      <svg width="18" height="18" viewBox="0 0 24 24"><path d="M7 10v11H3V10zM7 10l4-7c1.5 0 2.5 1 2 3l-1 4h7c1 0 2 1 1.7 2.2l-1.8 7c-.3.8-1 1.3-1.9 1.3H7" fill="none" stroke="#bbb" stroke-width="1.6"/></svg>
    </div>
    <span class="btn"></span>
    <span class="txt">You and 4.1k others like this.</span>
  </div>
</section>

<footer class="footer">
  <h3 style="left:52px">Contact Us</h3>
  <h3 style="left:543px">Headquarters</h3>
  <h3 style="left:896px">Blog Posts</h3>
  <div class="contact">
    <p>Please feel free to contact us for any issue. Our staff is available to you from 9AM until 5PM on weekdays.</p>
    <p>Phone: +1 480-555-2046</p>
    <p>Office: 412 Alder Lane, Mesa</p>
    <p>Email: info@borvicoheating.com</p>
  </div>
  <div class="social-row"><i></i><i></i><i></i><i></i><i></i></div>
  <div class="map" role="img" aria-label="Street map showing the headquarters location"></div>
  <div class="post" style="top:84px"><span class="thumb" role="img" aria-label="Blog post thumbnail"></span><div><div class="t">Business Cards Design Trends</div><div class="d">Dec 02, 2020 / 2 comments</div></div></div>
  <div class="post" style="top:156px"><span class="thumb" role="img" aria-label="Blog post thumbnail"></span><div><div class="t">This Maravelous App</div><div class="d">Nov 18, 2020 / 9 comments</div></div></div>
  <div class="post" style="top:228px"><span class="thumb" role="img" aria-label="Blog post thumbnail"></span><div><div class="t">Brand Paper Niceties</div><div class="d">Nov 10, 2020 / 0 comments</div></div></div>
  <div class="divider"></div>
  <div class="copy">Copyright 2020. All Rights Reserved by Borvico Heating</div>
</footer>

</body>
</html>
```